Business card design needed to incorporate existing logo

We need a business card for a new modern Accounting & Business Solutions company call TelmaNord Partners.com.au servicing all of Australia.
My tagline is Steady Ledger Answers... that deliver.

We specialise in Cloud Accounting and this is our primary focus. We also provide tax representation, debt recovery, computer, tablet and smart phone sales.

I would like a design that uses my corporate, trustworthy colours of blue/white, black/grey however am open to suggestion. I have attached my logo to go on the card somewhere,of which you will see the colour scheme.

I am after a card that STANDS OUT, somewhere between it not being too busy and not being a baron waste of space.

A 'cloud' incorporated in the design may work well, up to your artistic judgement. I know what I like when I see it; it is harder to put into words!

Excited to see your ideas!
I have added my logo predominately (blue/white) and for additional opportunity have added my reverse logo (darker one). I have used the blue/white on my website and letterhead. I will be using both on my vehicle signage.

Target Market(s)

Tradesmen and small-medium businesses of all descriptions Australia-wide

Industry/Entity Type

Debt

Contact Information for Business Card

Doug Hallett
Principal (optional)
TelmaNord Partners.com.au
Steady Ledger Answers... that deliver

P: 1800 493 518
M: 0412 658 071 (optional)
W: www.telmanordpartners.com.au
E: admin@telmanordpartners.com.au

Logo Text

Steady Ledger Answers... that deliver!

Logo styles of interest
Wordmark Logo
Requirements
Must have
• Must look professional and of high quality not cheap.

My logo and my tagline 'Steady Ledger Answers... that deliver'.

I have my colourscheme in mind as per my attached logo, however am open to suggestion. I want to see what you can create that I would not have thought of.

Modern, innovative.
Something I won't look at and think, 'I could have done that myself'.

Must be able to be printed on Prinvo 300gm premium cards and the artwork provided to me.
Nice to have
• Title of Principal is optional depending on space and judement call of look/fee.
M: (mobile) number is also optional as above.

Somthing cloud related given the Cloud Accounting aspect may be relevant. I leave it to your artistic design and judgement.
Should not have
• Must not look cheap.

```html
<!DOCTYPE html>
<html lang="en">
<head>
<meta charset="utf-8">
<title>TelmaNord Partners – Business Card</title>
<link href="https://fonts.googleapis.com/css2?family=Open+Sans:wght@400;600;700;800&display=swap" rel="stylesheet">
<style>
  :root {
    --navy: #1d2a5e;
    --sky: #2d8ed3;
    --brand-blue: #3a7fc1;
    --white: #ffffff;
    --stage: #2a2a2a;
    --cloud-light: #cfe6f7;
    --cloud-mid: #8fc4ea;
  }
  * { margin: 0; padding: 0; box-sizing: border-box; }
  html, body { width: 1200px; height: 1200px; overflow: hidden; }
  body {
    background: var(--stage);
    font-family: "Open Sans", sans-serif;
    display: flex;
    flex-direction: column;
    align-items: center;
    justify-content: center;
    gap: 60px;
  }
  .card {
    position: relative;
    width: 900px;
    height: 514px;
    background: var(--white);
    overflow: hidden;
  }

  /* ---------- Brand name ---------- */
  .brand {
    position: absolute;
    display: flex;
    align-items: center;
    gap: 10px;
    font-weight: 600;
    font-size: 21px;
    white-space: nowrap;
  }
  .brand-dot {
    width: 16px; height: 16px;
    border-radius: 50%;
    background: var(--sky);
    flex: none;
  }

  /* ---------- Front ---------- */
  .front-panel {
    position: absolute;
    left: 0; top: 0;
    width: 380px; height: 100%;
    background: var(--navy);
  }
  .front-stripe {
    position: absolute;
    left: 0; top: 440px;
    width: 380px; height: 16px;
    background: var(--sky);
  }
  .front-stripe-line {
    position: absolute;
    left: 0; top: 462px;
    width: 380px; height: 4px;
    background: var(--white);
  }
  .front .brand {
    left: 28px; top: 150px;
    color: var(--white);
  }
  .device-art {
    position: absolute;
    left: 440px; top: 30px;
    width: 420px; height: 330px;
    border-radius: 10px;
    background: radial-gradient(ellipse at 40% 30%, var(--cloud-light), var(--cloud-mid) 55%, #e9eff5 80%);
  }
  .front-web {
    position: absolute;
    left: 0; top: 392px;
    width: 100%;
    height: 44px;
    font-size: 30px;
    letter-spacing: 3px;
    font-weight: 600;
    white-space: nowrap;
  }
  .front-web .on-navy { color: var(--white); position: absolute; right: 522px; bottom: 0; }
  .front-web .on-white { color: var(--navy); position: absolute; left: 382px; bottom: 0; }
  .front-web small { font-size: 18px; font-weight: 400; letter-spacing: 2px; }
  .front-web .www { font-size: 16px; font-weight: 400; }

  /* ---------- Back ---------- */
  .back-divider {
    position: absolute;
    left: 390px; top: 0;
    width: 20px; height: 100%;
    background: var(--navy);
  }
  .back-panel {
    position: absolute;
    left: 424px; top: 0;
    width: 476px; height: 100%;
    background: var(--navy);
  }
  .back .brand {
    left: 28px; top: 244px;
    color: var(--brand-blue);
  }
  .contact {
    position: absolute;
    left: 462px; top: 70px;
    color: var(--white);
    font-weight: 700;
  }
  .contact-name { font-size: 34px; font-weight: 800; line-height: 1.2; }
  .contact-title { font-size: 26px; font-weight: 800; line-height: 1.3; margin-bottom: 18px; }
  .contact-company, .contact-tagline { font-size: 19px; line-height: 1.35; }
  .contact-tagline { margin-bottom: 26px; }
  .contact-lines { list-style: none; font-size: 17px; line-height: 1.75; }
</style>
</head>
<body>

  <section class="card front">
    <div class="front-panel"></div>
    <div class="front-stripe"></div>
    <div class="front-stripe-line"></div>
    <div class="brand"><span class="brand-dot"></span>TelmaNord Partners.com.au</div>
    <div class="device-art" role="img" aria-label="Illustration of a cloud connected to a laptop, smartphone and tablets"></div>
    <div class="front-web">
      <span class="on-navy"><span class="www">www.</span>telmanord</span>
      <span class="on-white">partners<small>.com.au</small></span>
    </div>
  </section>

  <section class="card back">
    <div class="back-divider"></div>
    <div class="back-panel"></div>
    <div class="brand"><span class="brand-dot"></span>TelmaNord Partners.com.au</div>
    <div class="contact">
      <p class="contact-name">Doug Hallett</p>
      <p class="contact-title">Principal</p>
      <p class="contact-company">TelmaNord Partners.com.au</p>
      <p class="contact-tagline">Steady Ledger Answers</p>
      <ul class="contact-lines">
        <li>P: 1800 493 518</li>
        <li>M: 0412 658 071</li>
        <li>E: admin@telmanordpartners.com.au</li>
        <li>W: www.telmanordpartners.com.au</li>
      </ul>
    </div>
  </section>

</body>
</html>
```